Brimsett Gardening Fresh New Website

We are looking to create a simple fresh website for our landscaping business. The website should appeal to a 'high end' audience. We deal with a lot of Embassies and affluent clients who have extremely large gardens that are meticulously maintained. The site is about communicating our excellent landscaping and customer service skills and encouraging new clients to reach out and engage us to take care of their gardens.

The website is basically going to be our business card, it will have almost no functionality other than two 'contact us' forms, one for smaller clients and one for more detailed projects.

The website will not have a lot of written content and will have to show photos of beautifully landscaped gardens.

The main logo in black will influence the site, however, we are open to all suggestions.

We are expecting to have the following pages:
Home Page
Services
About Us
Contact Us
Showcase (photo gallery of our work)

We need someone who can code it to wordpress and be available for minor changes over a number of days. They will be simple tweaks.

```html
<!DOCTYPE html>
<html lang="en">
<head>
<meta charset="utf-8">
<title>Brimsett Gardening</title>
<link rel="stylesheet" href="https://fonts.googleapis.com/css2?family=Libre+Baskerville:wght@400;700&family=Poppins:wght@400;500;600;700&family=Roboto:wght@400;500&display=swap">
<style>
:root{
  --gold:#b8862b;
  --gold-light:#f4d03f;
  --gold-mid:#e0ab2e;
  --ink:#111111;
  --dark:#141414;
  --white:#ffffff;
  --text:#222222;
  --forest:#3f5a2a;
  --forest-dark:#24351a;
}
*{margin:0;padding:0;box-sizing:border-box}
html,body{width:1200px;height:3080px;overflow:hidden;background:var(--white)}
body{position:relative;font-family:'Roboto',sans-serif;color:var(--text)}
.abs{position:absolute}
.serif{font-family:'Libre Baskerville',serif}
.gold-text{color:var(--gold)}
.gold-grad{background:linear-gradient(90deg,var(--gold),var(--gold-light))}

/* hero */
.hero{left:0;top:0;width:1200px;height:585px;background:linear-gradient(180deg,#2f4a22 0%,#5f7d3a 45%,#6f8f3e 70%,#4d6b2b 100%)}
.hero-shade{inset:0;background:rgba(0,0,0,.28)}
.nav-line{left:0;width:1200px;height:2px;background:var(--gold-mid);opacity:.85}
.brand-badge{left:142px;top:13px;width:122px;height:122px;border-radius:50%;background:#102218;border:2px solid #fff;display:flex;flex-direction:column;align-items:center;justify-content:center;color:#fff;font-family:'Libre Baskerville',serif;font-size:10px;letter-spacing:3px;line-height:1.5;text-align:center}
.nav{top:64px;left:590px;display:flex;gap:30px;font-family:'Poppins',sans-serif;font-weight:500;font-size:15px;color:#fff}
.nav-cta{left:947px;top:55px;width:112px;height:38px;border-radius:19px;background:linear-gradient(90deg,var(--gold-mid),var(--gold-light));color:#fff;font-family:'Poppins',sans-serif;font-weight:600;font-size:12px;display:flex;align-items:center;justify-content:center}
.hero-title{left:0;width:1200px;top:218px;text-align:center;font-family:'Poppins',sans-serif;font-weight:700;font-size:48px;color:#fff;line-height:63px}
.hero-title span{color:var(--gold-mid)}
.hero-text{left:150px;width:900px;top:356px;text-align:center;font-family:'Poppins',sans-serif;font-weight:500;font-size:13px;line-height:21px;color:#fff}
.hero-btn{left:544px;top:422px;width:112px;height:38px;border-radius:19px;background:#fff;color:#111;font-family:'Poppins',sans-serif;font-weight:500;font-size:12.5px;display:flex;align-items:center;justify-content:center}
.scroll-cue{left:568px;top:552px;width:64px;height:64px;border-radius:50%;background:#fff;box-shadow:0 6px 18px rgba(0,0,0,.12);display:flex;align-items:center;justify-content:center}

/* about */
.about-h{left:141px;top:680px;font-size:36px;font-weight:700;line-height:46px;color:var(--ink)}
.about-h .gold-text{display:block}
.about-p{left:141px;width:445px;font-size:12.5px;line-height:22.6px;color:var(--text)}
.btn-gold{background:linear-gradient(90deg,var(--gold),var(--gold-light));color:#1a1a1a;font-weight:500;font-size:12.5px;display:flex;align-items:center;justify-content:center}
.quote-card{left:694px;top:632px;width:371px;height:393px;background:var(--dark);border:6px solid var(--gold);border-top:none}
.quote-title{left:28px;top:4px;font-size:21px;color:#fff}
.field{left:28px;width:315px;height:35px;border:1px solid #e5e5e5;color:#fff;font-size:12.5px;padding:0 13px;display:flex;align-items:center}
.field i{color:#e02020;font-style:normal}

/* services */
.services-band{left:0;top:1112px;width:1200px;height:336px;background:linear-gradient(180deg,#3c5530 0%,#5a4a35 55%,#6a7d3a 100%)}
.services-shade{left:0;top:1112px;width:1200px;height:336px;background:rgba(0,0,0,.35)}
.section-title{left:0;width:1200px;text-align:center;font-family:'Libre Baskerville',serif;font-weight:700;color:var(--ink)}
.service-ring{width:276px;height:276px;border-radius:50%}
.service-photo{border-radius:50%;width:266px;height:266px;left:5px;top:0}
.service-label{width:320px;text-align:center;font-size:16.5px;font-weight:700}

/* reviews */
.review-box{left:282px;top:1727px;width:635px;height:164px;border:1.5px solid var(--gold);border-top-left-radius:48px}
.review-text{left:50px;width:535px;top:38px;text-align:center;font-size:12.5px;line-height:22.6px}
.review-author{left:0;width:635px;top:116px;text-align:center;font-weight:500;font-size:14px}
.arrow{width:26px;height:26px}

/* cta */
.cta-band{left:0;top:1999px;width:1200px;height:431px;background:linear-gradient(180deg,#4b5a3c 0%,#3a3a34 55%,#2e2c2a 100%)}
.cta-shade{left:0;top:1999px;width:1200px;height:431px;background:rgba(0,0,0,.35)}
.cta-text{left:200px;width:800px;top:2192px;text-align:center;color:#fff;font-size:12.5px;line-height:22.6px}

/* gallery */
.footer-band{left:0;top:2700px;width:1200px;height:345px;background:var(--dark)}
.gallery-tile{top:2588px;width:175px;height:171px}
.footer-nav{top:2862px;left:404px;width:653px;display:flex;justify-content:space-between;color:#fff;font-size:12.5px}
.footer-rule{left:404px;top:2904px;width:653px;height:1px;background:#3a3a3a}
.contact-item{top:2934px;display:flex;align-items:center;gap:14px;color:#fff;font-size:12.5px;line-height:16px}
.contact-icon{width:36px;height:36px;border-radius:50%;background:linear-gradient(135deg,var(--gold),var(--gold-light));display:flex;align-items:center;justify-content:center}
.footer-brand{left:130px;top:2920px;width:170px;text-align:center;color:var(--gold-mid);font-family:'Libre Baskerville',serif;font-size:18px;letter-spacing:5px;line-height:26px}
.footer-brand small{display:block;font-size:11px;letter-spacing:7px}
.legal-bar{left:0;top:3045px;width:1200px;height:35px;background:linear-gradient(90deg,var(--gold),var(--gold-light));display:flex;align-items:center;justify-content:space-between;padding:0 143px 0 141px;font-size:12px;color:#1a1a1a}
.social{display:flex;gap:12px}
.social span{width:14px;height:14px;border:1.5px solid #1a1a1a;border-radius:3px;display:block}
</style>
</head>
<body>

<!-- Hero -->
<section class="abs hero" role="img" aria-label="Forest garden with waterfall and stone steps through lawn"></section>
<div class="abs hero-shade" style="height:585px"></div>
<div class="abs nav-line" style="top:42px"></div>
<div class="abs nav-line" style="top:104px"></div>
<div class="abs brand-badge">BRIMSETT<br>GARDENING</div>
<nav class="abs nav"><span>Home</span><span>About Us</span><span>Services</span><span>Our Gallery</span></nav>
<div class="abs nav-cta">CONTACT US</div>
<h1 class="abs hero-title">BRIMSETT <span>LANDSCAPING</span><br>Gardening</h1>
<p class="abs hero-text">Lorem ipsum dolor sit amet, consectetur adipiscing elit, sed do eiusmod tempor incididunt ut labore et dolore magna aliqua.<br>Quis ipsum suspendisse ultrices gravida. Risus commodo viverra maecenas accumsan lacus vel facilisis.</p>
<div class="abs hero-btn">READ MORE</div>
<div class="abs scroll-cue">
  <svg width="24" height="40" viewBox="0 0 24 40"><rect x="2" y="2" width="20" height="36" rx="10" fill="none" stroke="#111" stroke-width="2.5"/><line x1="12" y1="9" x2="12" y2="17" stroke="#111" stroke-width="2.5" stroke-linecap="round"/></svg>
</div>

<!-- About -->
<h2 class="abs about-h serif">About<span class="gold-text">Brimsett Gardening</span></h2>
<p class="abs about-p" style="top:780px">Lorem Ipsum Is Simply Dummy Text Of The Printing And Typesetting Industry. Lorem Ipsum Has Been The Industry's Standard Dummy Text Ever Since The 1500s, When An Unknown Printer Took A Galley Of Type And Scrambled It To Make A Type Specimen Book.</p>
<p class="abs about-p" style="top:877px">Lorem Ipsum Is Simply Dummy Text Of The Printing And Typesetting Industry. Lorem Ipsum Has Been The Industry's Standard Dummy Text Ever Since The 1500s, When &nbsp;And Scrambled It To Make A Type Specimen Book.</p>
<div class="abs btn-gold" style="left:141px;top:962px;width:94px;height:34px">Read More</div>

<div class="abs quote-card">
  <div class="abs quote-title serif">Landscape Services</div>
  <div class="abs field" style="top:40px">Name<i>*</i></div>
  <div class="abs field" style="top:82px">Email<i>*</i></div>
  <div class="abs field" style="top:125px">Phone Number<i>*</i></div>
  <div class="abs field" style="top:167px">Street Address &amp; Zip Code<i>*</i></div>
  <div class="abs field" style="top:210px;justify-content:space-between">Which Service Would You Like A Bill For?
    <svg width="14" height="9" viewBox="0 0 14 9"><path d="M1 1l6 6 6-6" fill="none" stroke="#fff" stroke-width="2"/></svg></div>
  <div class="abs field" style="top:252px;height:70px;align-items:flex-start;padding-top:10px">Message</div>
  <div class="abs btn-gold" style="left:28px;top:330px;width:315px;height:33px">Request A Quote</div>
</div>

<!-- Services -->
<section class="abs services-band" role="img" aria-label="Garden lawn with wooden pergola and picnic tables"></section>
<div class="abs services-shade"></div>
<h2 class="abs section-title" style="top:1188px;font-size:36px;color:#fff">Our <span class="gold-text">Services</span></h2>

<div class="abs service-ring" style="left:141px;top:1258px;background:var(--gold-light)">
  <div class="abs service-photo" role="img" aria-label="Flowering shrubs and green lawn" style="background:linear-gradient(160deg,#8fbf5a,#d8507a 50%,#4f9a2a)"></div>
</div>
<div class="abs service-ring" style="left:461px;top:1258px;background:var(--gold)">
  <div class="abs service-photo" role="img" aria-label="Patio with outdoor sofas and woven poufs" style="background:linear-gradient(180deg,#b9c4cc,#dcdcd6 55%,#c8b49a)"></div>
</div>
<div class="abs service-ring" style="left:783px;top:1258px;background:var(--gold-light)">
  <div class="abs service-photo" role="img" aria-label="Gloved hand spraying leafy plants" style="background:linear-gradient(160deg,#6f9a48,#3f6a2c 60%,#203a7a)"></div>
</div>
<div class="abs service-label serif" style="left:119px;top:1552px">Lawn Fertilizing</div>
<div class="abs service-label serif gold-text" style="left:439px;top:1552px">Patios</div>
<div class="abs service-label serif" style="left:761px;top:1552px">Weed Control</div>

<!-- Reviews -->
<h2 class="abs section-title" style="top:1650px;font-size:36px">Customer <span class="gold-text">Reviews</span></h2>
<svg class="abs arrow" style="left:227px;top:1807px" viewBox="0 0 26 26"><circle cx="13" cy="13" r="11.5" fill="none" stroke="#111" stroke-width="1.8"/><path d="M15 8l-5 5 5 5" fill="none" stroke="#111" stroke-width="1.8"/></svg>
<svg class="abs arrow" style="left:944px;top:1807px" viewBox="0 0 26 26"><circle cx="13" cy="13" r="11.5" fill="none" stroke="#111" stroke-width="1.8"/><path d="M11 8l5 5-5 5" fill="none" stroke="#111" stroke-width="1.8"/></svg>
<div class="abs review-box">
  <p class="abs review-text">Lorem Ipsum Is Simply Dummy Text Of The Printing And Typesetting Industry. Lorem Ipsum Has Been The Industry's Standard Dummy Text Ever Since The 1500s, When An Unknown Printer Took A Galley Of Type And Scrambled It To Make A Type Specimen Book.</p>
  <div class="abs review-author">– Dana. R</div>
</div>

<!-- CTA -->
<section class="abs cta-band" role="img" aria-label="Covered terrace with sofas, coffee table and potted plants"></section>
<div class="abs cta-shade"></div>
<h2 class="abs section-title" style="top:2135px;font-size:38px;color:#fff">Build Your Outdoor Dream With Us</h2>
<p class="abs cta-text">Lorem Ipsum Is Simply Dummy Text Of The Printing And Typesetting Industry. Lorem Ipsum Has Been The Industry's Standard Dummy Text Ever Since The 1500s, When An Unknown Printer Took A Galley Of Type And Scrambled It To Make A Type Specimen Book.</p>
<div class="abs btn-gold" style="left:551px;top:2253px;width:98px;height:34px;background:var(--gold-mid)">Contact Us</div>

<!-- Gallery -->
<h2 class="abs section-title" style="top:2524px;font-size:36px">Work <span class="gold-text">Gallery</span></h2>
<div class="abs footer-band"></div>
<div class="abs gallery-tile" style="left:141px;background:linear-gradient(180deg,#7a9a6a,#4d7a2a 50%,#8ac03a)" role="img" aria-label="Golf course fairway lined with pine trees"></div>
<div class="abs gallery-tile" style="left:326px;background:linear-gradient(160deg,#a8cf6a,#4f8a2a)" role="img" aria-label="Hand holding a young green plant"></div>
<div class="abs gallery-tile" style="left:512px;background:linear-gradient(180deg,#6a8a4a,#8a8460 50%,#7a9a4a)" role="img" aria-label="Rolled hay bale on grass"></div>
<div class="abs gallery-tile" style="left:697px;background:linear-gradient(180deg,#8ab0d8,#4f9a2a 45%,#b87a6a)" role="img" aria-label="Park path curving through trees"></div>
<div class="abs gallery-tile" style="left:883px;background:linear-gradient(180deg,#5f8a3a,#6e5a3a 70%)" role="img" aria-label="Worker laying turf rolls on soil"></div>

<!-- Footer -->
<div class="abs footer-brand">
  <svg width="36" height="36" viewBox="0 0 36 36" style="display:block;margin:0 auto 14px"><circle cx="18" cy="18" r="16" fill="none" stroke="var(--gold-mid)" stroke-width="2"/></svg>
  BRIMSETT<small>GARDENING</small>
</div>
<nav class="abs footer-nav"><span>Home</span><span>Services</span><span>Gallery</span><span>About Us</span><span>Project Me</span><span>Contact Us</span></nav>
<div class="abs footer-rule"></div>
<div class="abs contact-item" style="left:401px">
  <span class="contact-icon"><svg width="16" height="18" viewBox="0 0 16 18"><path d="M8 17s6-6 6-10A6 6 0 0 0 2 7c0 4 6 10 6 10z" fill="none" stroke="#1a1a1a" stroke-width="1.6"/><circle cx="8" cy="7" r="2" fill="none" stroke="#1a1a1a" stroke-width="1.6"/></svg></span>
  <span>123, Street Name, City<br>Name, Country Name, &nbsp;1234</span>
</div>
<div class="abs contact-item" style="left:658px;top:2934px">
  <span class="contact-icon"><svg width="16" height="16" viewBox="0 0 16 16"><path d="M3 1.5l3 .5 1 3-2 1.5a9 9 0 0 0 4.5 4.5L11 9l3 1 .5 3-2 1.5C7 14 2 9 1.5 3.5z" fill="none" stroke="#1a1a1a" stroke-width="1.4"/></svg></span>
  <span>123 456 7890</span>
</div>
<div class="abs contact-item" style="left:843px">
  <span class="contact-icon"><svg width="16" height="12" viewBox="0 0 16 12"><rect x="1" y="1" width="14" height="10" rx="1" fill="none" stroke="#1a1a1a" stroke-width="1.4"/><path d="M1 2l7 5 7-5" fill="none" stroke="#1a1a1a" stroke-width="1.4"/></svg></span>
  <span>hello@brimsettgardening.com</span>
</div>
<div class="abs legal-bar">
  <span>© 2024 Brimsett Gardening. All Rights Reserved.</span>
  <span class="social"><span></span><span></span><span></span></span>
</div>

</body>
</html>
```